Home Page Design (+50 More Pages To Winning Designer!)

We have a 50+ page website, but we're starting with the home page. The winning designer will get all 50+ pages to design as a 2nd project, so make sure you do your best!

Velorane is in the private jet industry and needs a re-designed website.

We have created the structure for the website and content inside of Frandle.io (THESE ARE ONLY ROUGH A.I. GENERATED WIREFRAMES AND DO NOT NEED TO BE FOLLOWED EXACTLY) - https://www.frandle.io/app/project/K482915_qWmRtZaLs-KDnHoUvvy82QJ5cfhaR61trkwqlDV3Hm

Take the content from the 'Home Page' under the 'Wireframe' tab on the Frandle.io link above, but feel free to re-design the page in a better way as these are only A.I. generated wireframes.

We want a DARK theme.... High quality, luxurious feel, greyscale colors. Attached is a brand guideline (BUT THIS IS NOT A 100% BRAND GUIDELINE, YOU CAN CHANGE COLORS AND FONTS AND MAKE CHANGES IF YOU HAVE BETTER IDEAS) and attached is our logo. We are also attaching some examples of other apps and websites to give you a guideline of what we're looking for for this design project.

The final design MUST communicate luxury using high-quality imagery of large cabin luxurious private jets.
Updates

ENTRIES THAT DO NOT FOLLOW THE PROJECT BRIEF WILL BE AUTOMATICALLY DISCARDED. FOLLOW THE INSTRUCTIONS!

Industry/Entity Type

Travel

Number of Pages Required

1 page

Font styles to use
Sans Serif

Colors

Designer to choose colors to be used in the design.

Requirements
Must have
• Follow wireframe and use content in wireframe (see Frandle.io link)

```html
<!DOCTYPE html>
<html lang="en">
<head>
<meta charset="utf-8">
<title>Velorane — Private Jet Travel</title>
<link href="https://fonts.googleapis.com/css2?family=Lato:wght@300;400;700&display=swap" rel="stylesheet">
<style>
:root{
  --bg:#0b0b0b;
  --panel:#333333;
  --card:#3a3a3a;
  --text:#ffffff;
  --muted:#cfcfcf;
  --line:#5a5a5a;
  --gold:#f6d21c;
  --gold-light:#ffe45e;
  --ink:#141414;
}
*{box-sizing:border-box;margin:0;padding:0}
html,body{width:1200px;height:4563px;overflow:hidden;background:var(--bg);color:var(--text);font-family:'Lato',sans-serif}
.page{position:relative;width:1200px;height:4563px;overflow:hidden}
.abs{position:absolute}
h1,h2,h3,h4{font-weight:400}
p{font-weight:300}

/* header */
.brand{left:53px;top:38px;font-size:36px;font-weight:400;letter-spacing:-.5px;display:flex;align-items:center;gap:10px}
.brand .mark{width:22px;height:22px;background:var(--text);border-radius:4px}
.menu{left:1102px;top:38px;width:36px}
.menu span{display:block;height:3px;background:var(--text);margin-bottom:9px}

/* hero */
.hero-photo{left:0;top:0;width:1200px;height:700px;background:linear-gradient(180deg,#3b3a42 0%,#8a5a3a 30%,#c57a3e 42%,#4a4038 58%,#1c1a18 80%,#0b0b0b 100%)}
.hero-dots{left:1121px;top:595px}
.hero-dots span{display:block;width:16px;height:16px;border-radius:50%;background:#999;margin-bottom:21px}
.hero-dots span:first-child{background:#fff}
.hero-kicker{left:53px;top:688px;font-size:40px}
.hero-title{left:53px;top:740px;font-size:80px;line-height:1.1}
.hero-copy{left:53px;top:835px;width:1090px;font-size:27px;line-height:1.2;color:var(--muted)}
.rule{height:2px;background:var(--line)}

/* amenities */
.sec-title{font-size:80px;line-height:1.2}
.sec-lead{font-size:26px;line-height:1.22;color:var(--muted)}
.amenity{top:1340px;width:312px;background:var(--card)}
.amenity .photo{height:190px}
.amenity h3{font-size:30px;padding:10px 10px 0}
.amenity p{font-size:19px;line-height:1.27;padding:2px 10px 12px;color:var(--muted)}

/* features */
.features-photo{left:106px;top:1856px;width:465px;height:640px;background:linear-gradient(180deg,#bdbdbd,#8f8f8f)}
.feat-title{left:587px;top:1855px;font-size:52px;line-height:1.22}
.feat{width:255px}
.feat h4{font-size:30px;line-height:1.2}
.feat p{font-size:19px;line-height:1.27;color:var(--muted)}
.btn{display:flex;align-items:center;justify-content:space-between;background:var(--gold);color:#555;font-size:19px;padding:0 16px;height:48px;font-weight:300}
.btn svg{width:24px;height:14px}

/* benefits */
.benefits{left:53px;top:2565px;width:1094px;height:583px;background:var(--panel)}
.ben-col h4{font-size:30px}
.ben-col p{font-size:19px;line-height:1.27;color:var(--muted)}
.gold-rule{height:3px;background:var(--gold)}

/* testimonial */
.stars{left:0;top:3228px;width:1200px;text-align:center;color:var(--gold);font-size:40px;letter-spacing:6px}
.quote{left:106px;top:3280px;width:988px;text-align:center;font-size:28px;line-height:1.27}
.author{left:504px;top:3388px;display:flex;align-items:center;gap:10px}
.avatar{width:66px;height:66px;border-radius:50%;background:linear-gradient(180deg,#d9d9d9,#7a7a7a)}
.author b{display:block;font-weight:400;font-size:27px}
.author small{font-size:19px;color:var(--muted);font-weight:300}

/* partners */
.trusted{left:0;top:3536px;width:1200px;text-align:center;font-size:39px}
.partner{width:66px;height:66px;border-radius:14px;background:#4a4a4a}
.partner.round{border-radius:50%;background:#5a5a5a}

/* book */
.book-title{left:106px;top:3878px;width:470px;text-align:center;font-size:52px;line-height:1.22}
.book-copy{left:604px;top:3885px;width:490px;font-size:19px;line-height:1.27;color:var(--muted)}

/* footer */
.footer{left:0;top:4119px;width:1200px;height:444px;background:linear-gradient(180deg,var(--gold),var(--gold-light));color:var(--ink)}
.touch{left:106px;top:30px;font-size:52px}
.chat{left:106px;top:96px;width:988px;height:48px;background:var(--ink);color:var(--gold);display:flex;align-items:center;justify-content:space-between;padding:0 16px;font-size:19px}
.foot-rule{left:106px;top:166px;width:988px;height:2px;background:#8a7a20}
.foot-brand{left:106px;top:190px;font-size:30px;display:flex;align-items:center;gap:8px}
.foot-brand .mark{width:20px;height:20px;background:var(--ink);border-radius:3px}
.foot-col{top:196px;font-size:19px;line-height:35px;list-style:none;color:#5a4d0a;font-weight:300}
.foot-col li:first-child{color:var(--ink);font-weight:400}
.connect{left:930px;top:196px;font-size:19px;text-align:right;width:164px}
.socials{display:flex;gap:12px;justify-content:flex-end;margin-top:10px}
.socials span{width:26px;height:26px;border-radius:50%;background:var(--ink)}
</style>
</head>
<body>
<div class="page">

  <!-- hero -->
  <div class="abs hero-photo" role="img" aria-label="Private jet parked on a runway at sunset"></div>
  <div class="abs brand"><span>Velorane</span><span class="mark"></span></div>
  <div class="abs menu" aria-label="Menu"><span></span><span></span><span></span></div>
  <div class="abs hero-dots"><span></span><span></span><span></span></div>
  <p class="abs hero-kicker" style="font-weight:400">Welcome to Velorane</p>
  <h1 class="abs hero-title">Discover Unmatched Elegance</h1>
  <p class="abs hero-copy">Indulge in the ultimate luxury with Velorane. Step into a realm of opulence where every detail is meticulously crafted to cater to your every need. From our expansive cabin space to our unparalleled service, prepare to experience air travel like never before</p>
  <div class="abs rule" style="left:53px;top:982px;width:1094px"></div>

  <!-- amenities -->
  <h2 class="abs sec-title" style="left:106px;top:1040px;width:1000px">Explore Velorane's Premium Amenities</h2>
  <p class="abs sec-lead" style="left:106px;top:1233px;width:980px">Delve into the premium facilities offered by Velorane. From spacious cabins to unmatched personalized services, we provide an extraordinary experience for our customers.</p>

  <article class="abs amenity" style="left:106px">
    <div class="photo" role="img" aria-label="Luxurious jet cabin with leather seating" style="background:linear-gradient(180deg,#6b5330,#c7953e 55%,#5a4525)"></div>
    <h3>Spacious Cabins</h3>
    <p>Enjoy ample space to relax and unwind in our luxurious cabins, designed to provide the utmost comfort during your journey.</p>
  </article>
  <article class="abs amenity" style="left:443px">
    <div class="photo" role="img" aria-label="Pilot in a jet cockpit" style="background:linear-gradient(180deg,#3a3d44,#1a1b1e 60%,#2a2a2a)"></div>
    <h3>Exclusive Service</h3>
    <p>Our dedicated team ensures that your every need is met with personalized attention and impeccable service, making your journey with Velorane truly memorable.</p>
  </article>
  <article class="abs amenity" style="left:782px">
    <div class="photo" role="img" aria-label="Glowing global network of destinations" style="background:radial-gradient(circle at 50% 50%,#b87a2a,#3a2410 70%,#1a120a)"></div>
    <h3>Global Connectivity</h3>
    <p>With access to a wide range of destinations worldwide, Velorane offers unparalleled flexibility and convenience for your travel needs.</p>
  </article>
  <div class="abs rule" style="left:53px;top:1783px;width:1094px"></div>

  <!-- features -->
  <div class="abs features-photo" role="img" aria-label="Flight attendant demonstrating a life vest"></div>
  <h2 class="abs feat-title">Explore Our Latest Features</h2>
  <div class="abs feat" style="left:587px;top:2003px"><h4>Private Jet Lease Program</h4><p>A program allowing customers to lease private jets for a specified period without owning their own aircraft.</p></div>
  <div class="abs feat" style="left:849px;top:2003px"><h4>All Access Programs</h4><p>Programs providing exclusive access to various premium services and facilities offered by Velorane.</p></div>
  <div class="abs feat" style="left:587px;top:2225px"><h4>Helicopter Access Programs</h4><p>Programs offering helicopter access for quick and flexible transportation between airports, city centers, and other destinations.</p></div>
  <div class="abs feat" style="left:849px;top:2225px"><h4>By-the-Seat Charter Flights</h4><p>Seat charter flight services allowing customers to book seats on charter flights without having to charter the entire aircraft.</p></div>
  <a class="abs btn" style="left:587px;top:2448px;width:507px">Learn More<svg viewBox="0 0 24 14"><path d="M1 7h21M16 1l6 6-6 6" fill="none" stroke="#222" stroke-width="1.6"/></svg></a>

  <!-- benefits -->
  <section class="abs benefits">
    <h2 class="abs sec-title" style="left:53px;top:32px;width:900px">Benefits of Choosing Velorane</h2>
    <p class="abs" style="left:53px;top:228px;width:990px;font-size:20px;line-height:1.25;color:var(--muted)">Discover the myriad advantages that come with selecting Velorane for your air travel needs. From unparalleled comfort and flexibility to top-notch safety and convenience, explore why Velorane stands out as the premier choice for discerning travelers seeking a luxurious and seamless journey.</p>
    <div class="abs gold-rule" style="left:53px;top:307px;width:988px"></div>
    <div class="abs ben-col" style="left:53px;top:333px;width:490px"><h4>On-Demand Charter Services</h4><p>Enjoy flight flexibility with Velorane's on-demand charter services. Book a private jet anytime, anywhere, providing unparalleled comfort and flexibility in air travel.</p></div>
    <div class="abs ben-col" style="left:550px;top:333px;width:491px"><h4>Global Medical Response &amp; Recovery</h4><p>Safety and well-being are top priorities at Velorane. Our global medical response and recovery services offer additional protection while traveling, with swift access to emergency medical services worldwide and seamless recovery facilitation after medical incidents.</p></div>
    <a class="abs btn" style="left:53px;top:507px;width:988px">Learn More<svg viewBox="0 0 24 14"><path d="M1 7h21M16 1l6 6-6 6" fill="none" stroke="#222" stroke-width="1.6"/></svg></a>
  </section>

  <!-- testimonial -->
  <div class="abs rule" style="left:106px;top:3201px;width:988px"></div>
  <div class="abs stars">★★★★★</div>
  <p class="abs quote" style="font-weight:400">The experience with Velorane was truly exceptional. From the moment I booked my flight to the smooth landing, every detail was meticulously taken care of. I highly recommend Velorane to anyone seeking luxury air travel at its finest.</p>
  <div class="abs author"><div class="avatar" role="img" aria-label="Portrait of the reviewer"></div><div><b>Marcus Hale</b><small>Banker</small></div></div>
  <div class="abs rule" style="left:106px;top:3483px;width:988px"></div>

  <!-- partners -->
  <h3 class="abs trusted">Trusted by top-tier companies around the globe</h3>
  <div class="abs partner" style="left:401px;top:3614px"></div>
  <div class="abs partner round" style="left:511px;top:3614px"></div>
  <div class="abs partner" style="left:621px;top:3614px"></div>
  <div class="abs partner round" style="left:731px;top:3614px"></div>
  <div class="abs partner" style="left:456px;top:3707px"></div>
  <div class="abs partner round" style="left:566px;top:3707px"></div>
  <div class="abs partner" style="left:676px;top:3707px"></div>

  <!-- booking -->
  <h2 class="abs book-title">Book Your Journey with Velorane</h2>
  <p class="abs book-copy">Experience luxury air travel like never before with Velorane. Ready to embark on your next adventure? Booking with us is simple and hassle-free.</p>
  <a class="abs btn" style="left:604px;top:3963px;width:490px">Book<svg viewBox="0 0 24 14"><path d="M1 7h21M16 1l6 6-6 6" fill="none" stroke="#222" stroke-width="1.6"/></svg></a>

  <!-- footer -->
  <footer class="abs footer">
    <h2 class="abs touch">Let’s get in touch.</h2>
    <a class="abs chat">Come chat with us<svg viewBox="0 0 24 14" width="24" height="14"><path d="M1 7h21M16 1l6 6-6 6" fill="none" stroke="#f6d21c" stroke-width="1.6"/></svg></a>
    <div class="abs foot-rule"></div>
    <div class="abs foot-brand"><span>Velorane</span><span class="mark"></span></div>
    <ul class="abs foot-col" style="left:292px"><li>About US</li><li>Charter</li><li>Fleet</li><li>Destinations</li><li>Pricing</li><li>Contact</li></ul>
    <ul class="abs foot-col" style="left:505px"><li>Services</li><li>Private Jets</li><li>Helicopters</li><li>Jet Cards</li><li>Membership</li><li>FAQ</li></ul>
    <ul class="abs foot-col" style="left:720px"><li>Terms</li><li>Privacy</li><li>Careers</li><li>Press</li><li>Blog</li><li>Support</li></ul>
    <div class="abs connect">Connect With Us<div class="socials"><span></span><span></span><span></span><span></span></div></div>
  </footer>

</div>
</body>
</html>
```